Volunteer fire fighters needed banner

As part of our recruitment campaign, we need a sign we can post on our sign trailer to entice locals to join our volunteer fire service. This design will be printed on a banner, front and back, to catch traffic going in both directions on a busy roadway. This banner will have a printed surface of 4 feet tall by 8 feet long.
Our fire department is looking to attract people between the ages of 18 and 35 years old who are interested in being a firefighter. We offer our volunteers:
-Free professional training
-All equipment supplied
-Tax abatements for active volunteers
For more information, you can check us out at:
Brackenmoorfire.example

This design should:
-scale to and fit a 4'x8' canvas
-Include our web address "BrackenMoorFire.example"
-Say "Members Wanted"
-"Drill every Tuesday at 7pm"
-"57 Kestrel Pond Lane"
-Include "Bracken Moor Fire Department"

We've included reference photos and past images we use for our other campaigns for inspiration for you.

Target Market(s)

18-35 y/o

Industry/Entity Type

Fire Service

Requirements
Must have
• -scale to and fit a 4'x8' canvas -Include our web address "BrackenMoorFire.example" -Say "Members Wanted" -"Drill every Tuesday at 7pm" -"57 Kestrel Pond Lane" -Include "Bracken Moor Fire Department"

```html
<!DOCTYPE html>
<html lang="en">
<head>
<meta charset="utf-8">
<title>Local Heroes Wanted – Bracken Moor Fire Department</title>
<link rel="stylesheet" href="https://fonts.googleapis.com/css2?family=Lexend:wght@600;700;800&display=swap">
<style>
  :root {
    --sun: #fbb41a;
    --sun-light: #fde3b4;
    --ink: #2b2712;
    --navy: #34437a;
    --fire-red: #ec2227;
    --white: #ffffff;
  }
  * { margin: 0; padding: 0; box-sizing: border-box; }
  html, body { width: 1200px; height: 2400px; overflow: hidden; }
  body {
    position: relative;
    font-family: "Lexend", "Helvetica Neue", Arial, sans-serif;
    background:
      radial-gradient(ellipse 520px 420px at 620px 560px, rgba(253,227,180,.85), rgba(253,227,180,0) 70%),
      radial-gradient(ellipse 380px 300px at 1150px 1070px, rgba(253,232,196,.9), rgba(253,232,196,0) 70%),
      radial-gradient(ellipse 520px 360px at 120px 1500px, rgba(253,227,180,.75), rgba(253,227,180,0) 70%),
      radial-gradient(ellipse 460px 320px at 800px 1650px, rgba(253,227,180,.6), rgba(253,227,180,0) 70%),
      radial-gradient(ellipse 600px 260px at 350px 2050px, rgba(253,220,160,.45), rgba(253,220,160,0) 70%),
      var(--sun);
  }
  .headline { position: absolute; left: 0; top: 0; width: 1200px; height: 900px; }
  .headline text {
    font-family: "Lexend", "Helvetica Neue", Arial, sans-serif;
    font-weight: 800;
    font-size: 250px;
    fill: var(--sun);
    stroke: var(--ink);
    stroke-width: 10;
    stroke-linejoin: round;
    paint-order: stroke fill;
  }
  .drill {
    position: absolute; left: 0; width: 1200px; top: 1002px;
    text-align: center; color: var(--navy);
    font-weight: 600; font-size: 80px; letter-spacing: -1px;
  }
  .time-tag {
    position: absolute; left: 409px; top: 1120px; width: 383px; height: 100px;
    background: var(--navy); color: var(--white);
    font-weight: 600; font-size: 80px; line-height: 100px; text-align: center;
  }
  .address {
    position: absolute; left: 126px; top: 1316px; width: 949px; height: 128px;
    border: 3px solid var(--navy); color: var(--navy);
    font-weight: 600; font-size: 70px; line-height: 122px; text-align: center;
    letter-spacing: -1px; white-space: nowrap;
  }
  .department {
    position: absolute; left: 0; width: 1200px; top: 1522px;
    text-align: center; color: var(--fire-red);
    font-weight: 600; font-size: 78px; line-height: 80px;
  }
  .website {
    position: absolute; left: 0; width: 1200px; top: 1778px; height: 90px;
    display: flex; justify-content: center; align-items: center; gap: 14px;
    color: var(--fire-red); font-weight: 600; font-size: 60px;
  }
  .website svg { width: 78px; height: 78px; flex: none; }
  .department-mark {
    position: absolute; left: 0; width: 1200px; top: 2010px;
    display: flex; justify-content: center; align-items: center; gap: 24px;
    color: var(--fire-red); font-weight: 600; font-size: 64px;
  }
  .department-mark .dot {
    width: 90px; height: 90px; border-radius: 50%; background: var(--fire-red);
  }
  .members {
    position: absolute; left: 0; width: 1200px; top: 2190px;
    text-align: center; color: var(--navy);
    font-weight: 600; font-size: 64px; letter-spacing: 1px;
  }
</style>
</head>
<body>
  <svg class="headline" viewBox="0 0 1200 900" aria-label="Local Heroes Wanted">
    <text x="225" y="398" textLength="775" lengthAdjust="spacingAndGlyphs">LOCAL</text>
    <text x="127" y="632" textLength="966" lengthAdjust="spacingAndGlyphs">HEROES</text>
    <text x="86" y="865" textLength="1030" lengthAdjust="spacingAndGlyphs">WANTED</text>
  </svg>

  <div class="drill">DRILL EVERY TUESDAY</div>
  <div class="time-tag">AT 7PM</div>
  <div class="address">57 KESTREL POND LANE</div>

  <div class="department">Bracken Moor<br>Fire Department</div>

  <div class="website">
    <svg viewBox="0 0 80 80" fill="none" stroke="currentColor" stroke-width="4" aria-hidden="true">
      <circle cx="40" cy="40" r="36"/>
      <ellipse cx="40" cy="40" rx="16" ry="36"/>
      <line x1="40" y1="4" x2="40" y2="76"/>
      <line x1="4" y1="40" x2="76" y2="40"/>
      <line x1="10" y1="22" x2="70" y2="22"/>
      <line x1="10" y1="58" x2="70" y2="58"/>
    </svg>
    <span>BrackenMoorFire.example</span>
  </div>

  <div class="department-mark">
    <span class="dot"></span>
    <span>Bracken Moor Fire</span>
  </div>

  <div class="members">MEMBERS WANTED</div>
</body>
</html>
```